CM Candle Tube Packaging Design

Website: www.corvelmare.example
IG: @corvel.mare
Tagline: Elevate Your Ambiance
My brand is a sophisticated brand with luxury candles made of coconut wax. Im looking for an upscale minimalist chic design.
Discover the transformative power of positive energy with Corvel Mare candles. Indulge in true luxury with our specially crafted coconut wax blend that not only ignites captivating scents but also embodies modern elegance and empowering elements.
At Corvel Mare we're committed to delivering a unique and exhilarating aromatic experience to all candle lovers. Each candle is meticulously handcrafted in small batches using luxury fragrance oils exclusively formulated for coconut wax.
Our candles are:
Clean-burning
Paraben-Free
Phthalate-Free
Skin-Safe
Pet-Friendly

```html
<!DOCTYPE html>
<html lang="en">
<head>
<meta charset="utf-8">
<title>Corvel Mare — Candle Tube Packaging</title>
<link rel="stylesheet" href="https://fonts.googleapis.com/css2?family=Italiana&family=Montserrat:ital,wght@0,400;0,500;1,500&family=Allura&display=swap">
<style>
  :root {
    --backdrop: #f1e0e1;
    --wrap: #e2b3b0;
    --wrap-light: #ebc4c1;
    --lid: #e4b7b5;
    --lid-rim: #eec9c8;
    --seam: #cf9f9c;
    --ink: #2a2224;
    --white: #ffffff;
  }
  * { margin: 0; padding: 0; box-sizing: border-box; }
  html, body { width: 1200px; height: 1107px; overflow: hidden; }
  body { background: var(--backdrop); position: relative; font-family: "Montserrat", sans-serif; color: var(--ink); }

  .tube-wrap {
    position: absolute; left: 110px; top: 150px; width: 450px; height: 840px;
    background: linear-gradient(90deg, var(--wrap-light) 0%, var(--wrap) 55%, var(--wrap-light) 100%);
    overflow: hidden;
  }
  .tube-wrap__motif {
    position: absolute; left: 270px; top: 230px; width: 180px; height: 610px;
    background: linear-gradient(180deg, rgba(255,255,255,0) 0%, rgba(255,255,255,0.22) 40%, rgba(255,255,255,0.3) 100%);
  }
  .tube-wrap__seam { position: absolute; left: 0; right: 0; top: 245px; height: 1px; background: var(--seam); }
  .website { position: absolute; top: 190px; width: 100%; text-align: center; font-size: 13px; letter-spacing: 0.3px; }

  .wordmark {
    position: absolute; top: 420px; width: 100%; text-align: center;
    font-family: "Italiana", serif; font-size: 50px; letter-spacing: 1px; line-height: 1; text-transform: uppercase;
  }
  .descriptor {
    position: absolute; top: 495px; width: 100%;
    display: flex; align-items: center; justify-content: center; gap: 16px;
    font-size: 13px; letter-spacing: 5px; text-transform: uppercase;
  }
  .descriptor__rule { width: 22px; height: 1px; background: var(--ink); }
  .script-line { position: absolute; top: 525px; width: 100%; text-align: center; font-family: "Allura", cursive; font-size: 20px; }
  .tagline { position: absolute; top: 700px; width: 100%; text-align: center; font-size: 17px; font-style: italic; font-weight: 500; }
  .net-weight { position: absolute; top: 785px; width: 100%; text-align: center; font-size: 13px; }

  .lid {
    position: absolute; left: 645px; top: 395px; width: 430px; height: 430px; border-radius: 50%;
    background: var(--lid-rim); display: flex; align-items: center; justify-content: center;
  }
  .lid__face {
    width: 390px; height: 390px; border-radius: 50%; background: var(--lid);
    display: flex; align-items: center; justify-content: center;
  }
  .lid__monogram { font-family: "Italiana", serif; font-size: 110px; color: var(--white); letter-spacing: 2px; }
</style>
</head>
<body>
  <section class="tube-wrap">
    <div class="tube-wrap__motif" role="img" aria-label="Faint decorative flame motif"></div>
    <div class="tube-wrap__seam"></div>
    <p class="website">www.corvelmare.example</p>
    <h1 class="wordmark">Corvel Mare</h1>
    <p class="descriptor"><span class="descriptor__rule"></span>Handmade Candles<span class="descriptor__rule"></span></p>
    <p class="script-line">with purpose and love</p>
    <p class="tagline">Elevate Your Ambiance</p>
    <p class="net-weight">9 OZ/255G</p>
  </section>

  <section class="lid">
    <div class="lid__face"><span class="lid__monogram">CM</span></div>
  </section>
</body>
</html>
```